Multivitamin fruit drink in tetrapak

Label design for a 200 ml tetrapak which contains fruit juice with multivitamins in natural form . Product will be promoted to doctors and will follow a otx model. The target is children and women. Being a completely natural fortified multivitamin and mineral drink , the natural aspects to be highlighted. A white background is suggestive . Should not have more than 6 colors as this involves flexo printing.

Target Market(s)

Children and women through doctors recommendations

Industry/Entity Type

Pharmaceutical

Font styles to use
Serif
Sans Serif
Decorative

Requirements
Must have
• Pictures of fruit . Variant 1 is mango and variant 2 is orange. Brand name is Vordela. Can also suggest new names.
Nice to have
• The brand standing out, with white or softer color background
Should not have
• Should not have Dark background. Not funky or too colorful.

```html
<!DOCTYPE html>
<html lang="en">
<head>
<meta charset="utf-8">
<title>Vordela – Fruit Juice Label</title>
<link rel="stylesheet" href="https://fonts.googleapis.com/css2?family=Berkshire+Swash&family=Pinyon+Script&display=swap">
<style>
  :root {
    --paper: #ffffff;
    --brand-brown: #3a2211;
    --leaf-green: #5bb52a;
    --ink-dark: #2a1a0e;
    --peach-soft: #fbe6d4;
    --peach-mid: #f6d4b4;
    --mango-yellow: #e9b42a;
    --mango-orange: #f08a4a;
    --leaf-dark: #3f8a2a;
    --leaf-pale: #e6efe2;
  }
  * { margin: 0; padding: 0; box-sizing: border-box; }
  html, body { width: 1200px; height: 3000px; overflow: hidden; background: var(--paper); }
  .label {
    position: relative;
    width: 1200px;
    height: 3000px;
    background: var(--paper);
    overflow: hidden;
    font-family: "Berkshire Swash", cursive;
  }
  .leaf-decor {
    position: absolute;
    top: -40px; right: -60px;
    width: 760px; height: 720px;
    border-radius: 50%;
    background: radial-gradient(ellipse at 55% 45%, var(--leaf-pale) 0%, rgba(230,239,226,0.5) 45%, rgba(255,255,255,0) 72%);
  }
  .mango-backdrop {
    position: absolute;
    top: 500px; left: -160px;
    width: 1520px; height: 2300px;
    border-radius: 48%;
    background: radial-gradient(ellipse at 50% 45%, var(--peach-mid) 0%, var(--peach-soft) 45%, rgba(251,230,212,0.35) 70%, rgba(255,255,255,0) 82%);
  }
  .brand-name {
    position: absolute;
    top: 120px; left: 0; width: 1200px;
    text-align: center;
    font-family: "Berkshire Swash", cursive;
    font-size: 230px;
    line-height: 1;
    color: var(--brand-brown);
  }
  .claim {
    position: absolute;
    top: 600px; left: 0; width: 1200px;
    text-align: center;
    font-size: 88px;
    line-height: 140px;
    color: var(--leaf-green);
  }
  .fruit-photo {
    position: absolute;
    top: 1080px; left: 0;
    width: 1200px; height: 1160px;
    border-radius: 46% 46% 40% 40%;
    background:
      radial-gradient(ellipse at 50% 52%, var(--mango-orange) 0%, var(--mango-yellow) 38%, rgba(233,180,42,0) 62%),
      radial-gradient(ellipse at 50% 90%, var(--leaf-dark) 0%, rgba(63,138,42,0.6) 35%, rgba(255,255,255,0) 65%);
  }
  .juice-content {
    position: absolute;
    top: 2270px; left: 0; width: 1200px;
    text-align: center;
    font-family: "Pinyon Script", cursive;
    font-size: 150px;
    line-height: 1.2;
    color: var(--leaf-green);
  }
  .volume {
    position: absolute;
    bottom: 20px; right: 40px;
    font-size: 80px;
    color: var(--ink-dark);
  }
</style>
</head>
<body>
  <main class="label">
    <div class="leaf-decor" role="img" aria-label="Faint green leaf in the top corner"></div>
    <div class="mango-backdrop" role="img" aria-label="Large faded sliced mango behind the label"></div>
    <h1 class="brand-name">Vordela</h1>
    <p class="claim">Fortified<br>with natural<br>vitamins and minerals</p>
    <div class="fruit-photo" role="img" aria-label="Three ripe mangoes with water drops resting on green leaves"></div>
    <p class="juice-content">Fruit Juice 12%</p>
    <p class="volume">200ml</p>
  </main>
</body>
</html>
```